Tallow Crest - Facebook Cover Photo & Photo Icon Design

We’re looking for a Facebook Cover Photo and Profile Icon design for Tallow Crest, a leading Residential Real Estate brand under Kestmore Property Agents, based in Fenridge and Marlow Bay, Queensland, Australia.

This design will represent my professional real estate profile and needs to be bold, clean, and on-brand.

Deliverables:

Facebook Cover Photo (820 x 312 px, optimized for mobile + desktop)

Facebook Profile Icon (1:1 ratio, minimum 320 x 320 px)

Design Guidelines:

1. Must Include:

The Tallow Crest logo (provided after project start)

Use of the Kestmore Property Agents brand colour palette (will be supplied)

Clear connection to residential real estate

2. Optional but Preferred:

A local photo or skyline of Fenridge or Marlow Bay in QLD (bonus points for this)

Space for a short tagline like:
“Selling Faster. Selling Smarter. Selling Kestmore.”
(Optional tagline – open to variations if it improves layout/design)

3. Style & Feel:

Professional yet personable

Clean, modern aesthetic

Subtle touches of fun or personality are welcome

Layout must work well when overlaid by Facebook UI elements (like profile photo & call-to-action buttons)

Who I Am:
I'm a well-known residential real estate agent in the Redlands area, known for high-energy campaigns, premium video marketing, and a results-driven approach. My brand is fun, fresh, and high-performing — just like the real estate campaigns I run.

Files to be Provided (after selection):

Tallow Crest logo in high-res

Brand colour palette / style reference

Optional photo references if local imagery is not sourced by designer

Final Notes:

Make sure all text is legible on mobile and desktop

Original, layered design files must be delivered (PSD or AI preferred)

Bonus points if it feels uniquely “Bayside Queensland” while maintaining a national-level professional polish

Target Market(s)

Marlow Bay, Fenridge & Ashcombe

Industry/Entity Type

Real Estate

Colors
0054AA
0677BA
7BADD7
CADEEF
E8F1F8

Requirements
Must have
• Headshot, Mobile Number 0417 962 085, Suburbs - Marlow Bay, Fenridge & Ashcombe
Nice to have
• White, Crisp & Professional. Bottom Banner with Suburb List. Specialising in Marlow Bay, Fenridge & Ashcombe

```html
<!DOCTYPE html>
<html lang="en">
<head>
<meta charset="utf-8">
<title>Tallow Crest – Cover &amp; Profile Icon</title>
<link rel="stylesheet" href="https://fonts.googleapis.com/css2?family=Tinos:wght@700&family=PT+Sans+Narrow:wght@400;700&display=swap">
<style>
  :root {
    --navy: #0b1766;
    --ink: #0f1f6e;
    --rule: #8c9bc4;
    --accent: #f0a24b;
    --page: #eef1f5;
    --white: #ffffff;
    --ring: #2f6fe0;
  }
  * { margin: 0; padding: 0; box-sizing: border-box; }
  html, body { width: 1200px; height: 786px; overflow: hidden; background: var(--page); }
  .canvas { position: relative; width: 1200px; height: 786px; }

  .cover {
    position: absolute; left: 40px; top: 50px;
    width: 1120px; height: 421px;
    background: var(--white);
    overflow: hidden;
    border-radius: 6px;
  }
  .cover-art { position: absolute; inset: 0; width: 1120px; height: 421px; }

  .brand-name {
    position: absolute; left: 594px; top: 48px; transform: translateX(-50%);
    display: flex; flex-direction: column; align-items: center;
    font-family: "PT Sans Narrow", sans-serif; font-weight: 400;
    color: var(--navy); line-height: 1; white-space: nowrap;
  }
  .brand-name .line-sm { font-size: 22px; letter-spacing: 4px; }
  .brand-name .line-lg { font-size: 44px; letter-spacing: 5px; margin-top: 2px; }

  .agent-name {
    position: absolute; left: 340px; width: 500px; top: 128px;
    text-align: center;
    font-family: "Tinos", serif; font-weight: 700;
    font-size: 62px; line-height: 74px; letter-spacing: 2px; color: var(--navy);
    white-space: nowrap;
  }
  .tagline, .suburbs {
    position: absolute; left: 350px; width: 480px; text-align: center;
    font-family: "PT Sans Narrow", sans-serif; font-weight: 400;
    font-size: 25px; line-height: 30px;
    color: var(--ink); white-space: nowrap;
  }
  .tagline { top: 226px; }
  .suburbs { top: 261px; }
  .phone {
    position: absolute; left: 594px; top: 334px; transform: translateX(-50%);
    display: flex; align-items: center; gap: 8px;
    font-family: "Tinos", serif; font-weight: 700;
    font-size: 46px; line-height: 54px; color: var(--navy); white-space: nowrap;
  }
  .phone svg { width: 36px; height: 36px; }

  .profile-icon {
    position: absolute; left: 40px; top: 510px;
    width: 230px; height: 230px; border-radius: 50%;
    background: var(--white);
    border: 3px solid var(--ring);
    display: flex; align-items: center; justify-content: center;
  }
  .profile-disc {
    width: 212px; height: 212px; border-radius: 50%;
    background: var(--navy);
    display: flex; flex-direction: column; align-items: center; justify-content: center;
    font-family: "PT Sans Narrow", sans-serif; font-weight: 400;
    color: var(--white); letter-spacing: 4px; line-height: 1;
  }
  .profile-disc .line-sm { font-size: 20px; margin-bottom: 6px; }
  .profile-disc .line-lg { font-size: 40px; }
</style>
</head>
<body>
<div class="canvas">

  <section class="cover">
    <svg class="cover-art" viewBox="0 0 1120 421" xmlns="http://www.w3.org/2000/svg">
      <defs>
        <linearGradient id="skyline" x1="0" y1="0" x2="0" y2="1">
          <stop offset="0" stop-color="#3f5fd8"/>
          <stop offset="0.35" stop-color="#6f86d8"/>
          <stop offset="0.55" stop-color="#a4a7b4"/>
          <stop offset="0.75" stop-color="#7d7a6a"/>
          <stop offset="1" stop-color="#5d7a3a"/>
        </linearGradient>
        <linearGradient id="interior" x1="0" y1="0" x2="1" y2="0">
          <stop offset="0" stop-color="#ffffff"/>
          <stop offset="1" stop-color="#e9ebee"/>
        </linearGradient>
        <linearGradient id="headshot" x1="0" y1="0" x2="0" y2="1">
          <stop offset="0" stop-color="#e6e8ec"/>
          <stop offset="0.35" stop-color="#b9c0cc"/>
          <stop offset="1" stop-color="#2c3f63"/>
        </linearGradient>
      </defs>
      <rect x="760" y="0" width="360" height="421" fill="url(#interior)"/>
      <path role="img" aria-label="Photo of a city skyline beside a river with a bridge and parkland"
            d="M0 0 H250 C340 70 372 300 265 421 H0 Z" fill="url(#skyline)"/>
      <path role="img" aria-label="Headshot of the agent in a navy blazer and white shirt"
            d="M804 421 V300 C810 250 860 220 900 200 C905 140 930 50 990 42 C1050 50 1070 140 1060 200 C1090 215 1110 240 1120 270 V421 Z"
            fill="url(#headshot)"/>
      <line x1="350" y1="225" x2="830" y2="225" stroke="var(--rule)" stroke-width="1.5"/>
      <line x1="350" y1="258" x2="830" y2="258" stroke="var(--rule)" stroke-width="1.5"/>
      <rect x="0" y="417" width="807" height="4" fill="var(--accent)"/>
    </svg>

    <div class="brand-name">
      <span class="line-sm">TALLOW</span>
      <span class="line-lg">CREST</span>
    </div>
    <h1 class="agent-name">ROWAN ASHBY</h1>
    <p class="tagline">Selling Faster. Selling Smarter. Selling Kestmore.</p>
    <p class="suburbs">Suburbs - Marlow Bay, Fenridge &amp; Ashcombe</p>
    <div class="phone">
      <svg viewBox="0 0 36 36" aria-hidden="true">
        <circle cx="18" cy="18" r="17" fill="var(--navy)"/>
        <path d="M12.5 9.5c1-.6 2-.4 2.6.5l1.7 2.8c.5.9.3 1.9-.5 2.5l-1.1.8c.8 2 2.4 3.8 4.5 4.7l.8-1.1c.6-.8 1.7-1 2.5-.5l2.8 1.7c.9.6 1.1 1.6.5 2.6l-.9 1.3c-.9 1.3-2.6 1.8-4.1 1.2-5.1-2-8.9-5.8-10.9-10.9-.6-1.5-.1-3.2 1.200-4.1z" fill="var(--white)"/>
      </svg>
      <span>0417 962 085</span>
    </div>
  </section>

  <div class="profile-icon">
    <div class="profile-disc">
      <span class="line-sm">TALLOW</span>
      <span class="line-lg">CREST</span>
    </div>
  </div>

</div>
</body>
</html>
```